KAJU Freightways #ALLKAJU Business Cards & Letterhead

I am looking to business cards designed for our organization. We are currently undergoing a small re-branding that is taking place. Our organization is called KAJU Freightways and we are headquartered in Phoenix, AZ. We primarily provide transportation and logistics services to the Marlow Parcel Bureau who is our largest customer. I would like to see a design that incorporates name, title, contact info, website, and address (this will be different depending on the employee). I would also like to see some color on the business card using our logo colors or a variation. I would like our logo on the back of the business card with the website displayed. The final design should communicate that we are a next generation transportation operate that focuses on being driver-first, customer-centric, innovative, and sustainable.We would also like our #ALLKAJU catch phrase incorporated as well.

Target Market(s)

Transportation & Logistics

Industry/Entity Type

Trucking Company

Contact Information for Business Card

-First and Last Name
-Position Title
-Contact Phone
-Contact Email
-Physical Address

Font styles to use
Serif

Colors

Designer to choose colors to be used in the design.

Requirements
Must have
• -KAJU logo prominently displayed
• -#ALLKAJU catch phrase used
• -Some amount of color, design gradient, etc.
• -Logo on the back with website listed (https://www.kajufreightco.example)

```html
<!DOCTYPE html>
<html lang="en">
<head>
<meta charset="utf-8">
<title>KAJU Freightways — Letterhead &amp; Business Cards</title>
<link rel="stylesheet" href="https://fonts.googleapis.com/css2?family=Lato:wght@400;700&family=Ubuntu:wght@400&family=Arimo:wght@400;700&family=Cedarville+Cursive&display=swap">
<style>
  :root {
    --navy: #143a45;
    --green: #7bbb42;
    --paper: #f5f5f5;
    --backdrop: #e2e2e2;
    --ink: #1c1c1c;
    --faint: rgba(255,255,255,0.07);
  }
  * { margin: 0; padding: 0; box-sizing: border-box; }
  html, body { width: 1200px; height: 1200px; overflow: hidden; }
  body { background: var(--backdrop); position: relative; font-family: "Lato", sans-serif; }

  .letterhead { position: absolute; left: 104px; top: 165px; width: 669px; height: 863px; background: var(--paper); overflow: hidden; }
  .card { position: absolute; left: 822px; width: 276px; height: 157px; overflow: hidden; }
  .card-back { top: 286px; background: var(--navy); }
  .card-front { top: 466px; background: var(--paper); }

  .brand { position: absolute; display: flex; align-items: center; font-family: "Lato", sans-serif; font-weight: 700; color: var(--navy); letter-spacing: 0.5px; }
  .brand .dot { border-radius: 50%; background: var(--green); flex: none; }
  .brand--on-dark { color: #ffffff; }

  .divider { position: absolute; width: 1.5px; background: var(--navy); }
  .divider--light { background: var(--green); width: 1px; }
  .tagline { position: absolute; font-family: "Ubuntu", sans-serif; color: var(--green); line-height: 1.2; }

  /* letterhead header */
  .lh-brand { left: 30px; top: 70px; font-size: 30px; }
  .lh-brand .dot { width: 14px; height: 14px; margin-right: 8px; }
  .lh-divider { left: 149px; top: 43px; height: 84px; }
  .lh-tagline { left: 163px; top: 68px; font-size: 15.5px; line-height: 18px; }
  .lh-company { position: absolute; right: 52px; top: 46px; text-align: right; font-size: 9.8px; line-height: 12px; color: var(--navy); }
  .lh-company strong { font-weight: 700; }
  .lh-contacts { position: absolute; right: 52px; top: 88px; text-align: right; font-size: 9.8px; line-height: 12.3px; color: var(--navy); list-style: none; }
  .lh-contacts li { display: flex; justify-content: flex-end; align-items: center; gap: 3px; }
  .icon { width: 8px; height: 8px; flex: none; }

  /* letter body */
  .letter { position: absolute; left: 51px; top: 219px; width: 566px; font-family: "Arimo", sans-serif; font-size: 9.4px; line-height: 13.1px; color: var(--ink); }
  .letter p { margin-bottom: 13px; text-align: justify; }
  .letter .date { margin-bottom: 13px; }
  .letter .recipient { margin-bottom: 26px; text-align: left; }
  .letter .salutation { font-weight: 700; margin-bottom: 26px; }
  .letter .closing { margin-top: 33px; margin-bottom: 18px; }
  .letter .signature { font-family: "Cedarville Cursive", cursive; font-size: 17px; line-height: 20px; margin-bottom: 11px; }
  .letter .signer { text-align: left; }

  .swoosh { position: absolute; left: 0; top: 0; width: 100%; height: 100%; }
  .hashtag { font-family: "Lato", sans-serif; fill: #ffffff; }
  .hashtag .hash { fill: var(--green); }

  /* card back */
  .cb-brand { left: 53px; top: 67px; font-size: 16px; }
  .cb-brand .dot { width: 7px; height: 7px; margin-right: 4px; }
  .cb-divider { left: 122px; top: 52px; height: 55px; }
  .cb-tagline { left: 131px; top: 67px; font-size: 9px; line-height: 11px; }
  .cb-web { position: absolute; left: 0; width: 100%; top: 131px; text-align: center; font-size: 7.3px; color: #ffffff; letter-spacing: 0.6px; }
  .cb-web span { color: var(--green); }

  /* card front */
  .cf-brand { left: 19px; top: 33px; font-size: 16px; }
  .cf-brand .dot { width: 7px; height: 7px; margin-right: 4px; }
  .cf-person { position: absolute; right: 20px; top: 33px; text-align: right; }
  .cf-name { font-size: 9.5px; font-weight: 700; color: var(--green); letter-spacing: 0.2px; line-height: 11px; }
  .cf-title { font-size: 7.2px; color: var(--navy); line-height: 9px; }
  .cf-address { position: absolute; left: 19px; top: 77px; font-size: 7px; line-height: 9.3px; color: var(--navy); }
  .cf-address strong { font-weight: 700; }
  .cf-contacts { position: absolute; left: 19px; top: 108px; font-size: 7px; line-height: 9.6px; color: var(--navy); list-style: none; }
  .cf-contacts li { display: flex; align-items: center; gap: 3px; }
  .cf-contacts .icon { width: 6px; height: 6px; }
  .cf-contacts em { font-style: normal; color: var(--green); }
</style>
</head>
<body>

<!-- ===== Letterhead ===== -->
<article class="letterhead">
  <div class="brand lh-brand"><span class="dot"></span>KAJU</div>
  <div class="divider lh-divider"></div>
  <div class="tagline lh-tagline">Transportation<br>and Energy Services</div>

  <address class="lh-company" style="font-style:normal">
    <strong>KAJU Freightways &amp; Energy Services, Inc.</strong><br>
    4410 North Canyon Ridge Road<br>
    Glendale, AZ 85310
  </address>
  <ul class="lh-contacts">
    <li>602-555-0148
      <svg class="icon" viewBox="0 0 10 10"><path d="M2 1 L3.5 1 L4.3 3.2 L3.3 4 Q4.3 6 6 6.8 L6.8 5.8 L9 6.6 L9 8 Q9 9 8 9 Q1 8.5 1 2 Q1 1 2 1Z" fill="var(--green)"/></svg></li>
    <li>info@kajufreightco.example
      <svg class="icon" viewBox="0 0 10 10"><rect x="0.8" y="2" width="8.4" height="6" fill="none" stroke="var(--green)" stroke-width="0.9"/><path d="M0.8 2 L5 5.5 L9.2 2" fill="none" stroke="var(--green)" stroke-width="0.9"/></svg></li>
    <li>www.kajufreightco.example
      <svg class="icon" viewBox="0 0 10 10"><circle cx="5" cy="5" r="4" fill="none" stroke="var(--green)" stroke-width="0.8"/><ellipse cx="5" cy="5" rx="1.8" ry="4" fill="none" stroke="var(--green)" stroke-width="0.7"/><path d="M1 5 H9 M1.6 3 H8.4 M1.6 7 H8.4" stroke="var(--green)" stroke-width="0.6"/></svg></li>
  </ul>

  <section class="letter">
    <p class="date">November 15, 2019</p>
    <p class="recipient">Mr. John Doe<br>President<br>AA Corporation<br>111 Street Name, Suite#<br>City, State, 12345</p>
    <p class="salutation">Dear Mr. John,</p>
    <p>Lorem ipsum dolor sit amet, consectetur adipiscing elit. Integer diam quam, egestas eu ultrices eu, suscipit ac sapien. Phasellus eu dui nisi. Nam et euismod diam, nec lobortis tortor. Donec et diam nulla. Aenean varius tincidunt convallis. Aliquam a tortor at lacus dictum aliquet. Nunc laoreet metus sapien, in scelerisque augue consectetur in.</p>
    <p>Fusce nec justo laoreet, egestas justo sed, aliquet sem. Pellentesque pharetra massa non orci bibendum semper. Pellentesque cursus eu lectus a consectetur. Nunc volutpat suscipit posuere. Vestibulum facilisis vel quam malesuada mattis. Nulla in mattis tellus. Maecenas tristique mauris vitae pharetra tincidunt. In ut ornare risus. Integer molestie vestibulum nisi, semper dapibus mi condimentum eu.</p>
    <p>Nullam sagittis elit libero, id fringilla est tincidunt eget. Donec in ipsum ultricies, consectetur quam vel, facilisis elit. Phasellus tincidunt congue risus vel luctus. Suspendisse ut mollis neque. Donec ornare orci in turpis vestibulum, in ultrices metus scelerisque. Pellentesque mattis mattis nunc, nec tincidunt lacus egestas id. Fusce facilisis sagittis neque sit amet vulputate. Aliquam ut eros lobortis tortor facilisis vehicula. Sed sed luctus leo, at laoreet sapien. Donec placerat adipiscing ligula non euismod. In lobortis pretium nisl id luctus.</p>
    <p>Integer gravida tincidunt nibh, scelerisque tincidunt turpis. Suspendisse potenti. Nunc hendrerit euismod lectus id elementum. Fusce vitae gravida velit, quis eleifend lectus. In imperdiet mauris eu dui viverra sagittis. Donec tempor dui diam, condimentum gravida lacus pretium a. Nullam fringilla augue quis arcu placerat scelerisque. Aliquam nec tincidunt augue, sit amet posuere ipsum.</p>
    <p class="closing">Sincerely Yours,</p>
    <p class="signature">Dorian Kessler</p>
    <p class="signer">Dorian Kessler<br>President</p>
  </section>

  <svg class="swoosh" viewBox="0 0 1078 1390" preserveAspectRatio="none" aria-hidden="true">
    <path d="M0 1295 C300 1372 800 1322 1078 1127 L1078 1390 L0 1390 Z" fill="var(--green)"/>
    <path d="M0 1340 C260 1402 760 1388 1078 1127 L1078 1390 L0 1390 Z" fill="var(--navy)"/>
    <circle cx="935" cy="1328" r="125" fill="none" stroke="var(--faint)" stroke-width="7"/>
    <text class="hashtag" x="925" y="1335" font-size="19" text-anchor="middle"><tspan class="hash">#</tspan>ALLKAJU</text>
  </svg>
</article>

<!-- ===== Business card back ===== -->
<article class="card card-back">
  <div class="brand brand--on-dark cb-brand"><span class="dot"></span>KAJU</div>
  <div class="divider divider--light cb-divider"></div>
  <div class="tagline cb-tagline">Transportation<br>and Energy Services</div>
  <p class="cb-web">www.<span>kajufreightco</span>.example</p>
</article>

<!-- ===== Business card front ===== -->
<article class="card card-front">
  <div class="brand cf-brand"><span class="dot"></span>KAJU</div>
  <div class="cf-person">
    <p class="cf-name">DORIAN KESSLER</p>
    <p class="cf-title">President</p>
  </div>
  <address class="cf-address" style="font-style:normal">
    <strong>KAJU Freightways &amp; Energy Services, Inc.</strong><br>
    4410 North Canyon Ridge Road<br>
    Glendale, AZ 85310
  </address>
  <ul class="cf-contacts">
    <li><svg class="icon" viewBox="0 0 10 10"><path d="M2 1 L3.5 1 L4.3 3.2 L3.3 4 Q4.3 6 6 6.8 L6.8 5.8 L9 6.6 L9 8 Q9 9 8 9 Q1 8.5 1 2 Q1 1 2 1Z" fill="var(--green)"/></svg>602-555-0148</li>
    <li><svg class="icon" viewBox="0 0 10 10"><rect x="0.8" y="2" width="8.4" height="6" fill="none" stroke="var(--green)" stroke-width="1"/><path d="M0.8 2 L5 5.5 L9.2 2" fill="none" stroke="var(--green)" stroke-width="1"/></svg>dorian@kajufreightco.example</li>
    <li><svg class="icon" viewBox="0 0 10 10"><circle cx="5" cy="5" r="4" fill="none" stroke="var(--green)" stroke-width="0.9"/><path d="M1 5 H9 M5 1 V9" stroke="var(--green)" stroke-width="0.7"/></svg>www.<em>kajufreightco</em>.example</li>
  </ul>
  <svg class="swoosh" viewBox="0 0 444 253" preserveAspectRatio="none" aria-hidden="true">
    <path d="M0 214 C120 246 330 216 444 133 L444 253 L0 253 Z" fill="var(--green)"/>
    <path d="M0 227 C110 258 310 232 444 133 L444 253 L0 253 Z" fill="var(--navy)"/>
    <circle cx="377" cy="223" r="56" fill="none" stroke="var(--faint)" stroke-width="3"/>
    <text class="hashtag" x="377" y="227" font-size="12" text-anchor="middle"><tspan class="hash">#</tspan>ALLKAJU</text>
  </svg>
</article>

</body>
</html>
```